Business Cards for new orthopaedic surgery practice

My husband and I are starting our own orthopaedic surgery practice. We are looking for a business card that is uniform, but one will have my name/title and the other will have his. You can just create one design with my name on it for now. But when I choose your design as the winning design I will ask that you add another copy with his name/title.

We are looking for classy, simple, elite all in one. We like dark blues/a little gold/yellow. Something that goes with our logo. We want our logo incorporated. Here is all the info you need:
Business name: RV Bone & Vitality Center
Location: 38517 North Willowmere Ave
Coral Springs, FL 33071
Phone: 954-218-4063
Fax: 954-582-7341
Email: info@myrvbonecare.example

Names: Lydia Vance, M.D.
Board Certified Hand and Upper Extremity Surgeon

Ebo Dansu, M.D.
Board Certified Hip & Knee Replacement/General Orthopaedic Surgeon

Can decide what you want to put on the back. Maybe a slogan:
Rooted in Care. Focused on You

I am just going to upload our logo. The only thing is if we select you as the winning design, the location, and phone numbers may change. We will need your help to update that once fully solidified.

Industry/Entity Type

Medical

Contact Information for Business Card

Colors
0054AA
0677BA
7BADD7
CADEEF
E8F1F8
0094D4
00A9DD
6FCCEA
C7EBF8
E9F6FB

Requirements
Must have
• class, appeal,
Should not have
• We want to air on the side of masculine if we are looking at masculine vs. feminine feel. But we still want it classy, sophisticated, and something we will love

```html
<!DOCTYPE html>
<html lang="en">
<head>
<meta charset="utf-8">
<title>RV Bone &amp; Vitality Center – Business Card</title>
<link rel="stylesheet" href="https://fonts.googleapis.com/css2?family=Montserrat:wght@400;500;700&display=swap">
<style>
  :root {
    --navy: #233d7f;
    --navy-light: #4a64a0;
    --navy-ink: #25408a;
    --sky: #1bb8e0;
    --ink: #2e2e2e;
    --white: #ffffff;
    --tagline: #e3e9f5;
    --stage: #9a9a9a;
  }
  * { margin: 0; padding: 0; box-sizing: border-box; }
  html, body {
    width: 1200px; height: 1108px; overflow: hidden;
    background: var(--stage);
    font-family: "Montserrat", Arial, sans-serif;
  }
  .card {
    position: absolute; left: 242px; width: 716px; height: 409px;
    overflow: hidden;
  }
  /* Front */
  .card--front {
    top: 119px;
    background: linear-gradient(115deg, var(--navy) 0%, var(--navy) 38%, var(--navy-light) 52%, #34508f 68%, var(--navy) 90%);
    color: var(--white);
  }
  .brand {
    position: absolute; display: flex; align-items: center;
  }
  .brand__dot { border-radius: 50%; flex: none; }
  .brand__name { font-weight: 700; text-transform: uppercase; line-height: 1.08; }
  .card--front .brand { left: 78px; top: 150px; gap: 26px; }
  .card--front .brand__dot { width: 96px; height: 96px; background: var(--white); }
  .card--front .brand__name { font-size: 36px; color: var(--white); letter-spacing: 0.5px; }
  .tagline {
    position: absolute; left: 0; right: 0; top: 366px;
    text-align: center; font-size: 17px; color: var(--tagline); letter-spacing: 0.2px;
  }
  /* Back */
  .card--back { top: 581px; background: var(--white); color: var(--ink); }
  .card--back .brand { left: 0; right: 0; top: 30px; justify-content: center; gap: 14px; }
  .card--back .brand__dot { width: 46px; height: 46px; background: var(--navy-ink); }
  .card--back .brand__name { font-size: 19px; color: var(--navy-ink); }
  .doctor { position: absolute; left: 0; right: 0; text-align: center; }
  .doctor__name { font-size: 32px; font-weight: 700; color: var(--sky); line-height: 1; }
  .doctor__title { font-size: 16.5px; font-weight: 500; margin-top: 9px; letter-spacing: 0.2px; }
  .doctor--first { top: 155px; }
  .doctor--second { top: 227px; }
  .contact { position: absolute; top: 306px; font-size: 17px; line-height: 27px; font-weight: 500; }
  .contact--address { right: 369px; text-align: right; }
  .contact--address .practice { color: var(--sky); }
  .contact__divider { position: absolute; left: 373px; top: 310px; width: 2px; height: 71px; background: var(--sky); }
  .contact--lines { left: 401px; }
  .contact__row { display: flex; align-items: center; gap: 8px; }
  .contact__row svg { width: 16px; height: 14px; fill: var(--sky); flex: none; }
</style>
</head>
<body>
  <section class="card card--front">
    <div class="brand">
      <span class="brand__dot"></span>
      <span class="brand__name">RV Bone &amp;<br>Vitality Center</span>
    </div>
    <p class="tagline">Rooted in Care. Focused on You</p>
  </section>

  <section class="card card--back">
    <div class="brand">
      <span class="brand__dot"></span>
      <span class="brand__name">RV Bone &amp;<br>Vitality Center</span>
    </div>

    <div class="doctor doctor--first">
      <h2 class="doctor__name">Lydia Vance, M.D.</h2>
      <p class="doctor__title">Board Certified Hand and Upper Extremity Surgeon</p>
    </div>
    <div class="doctor doctor--second">
      <h2 class="doctor__name">Ebo Dansu, M.D.</h2>
      <p class="doctor__title">Board Certified Hip &amp; Knee Replacement/General Orthopaedic Surgeon</p>
    </div>

    <address class="contact contact--address" style="font-style:normal">
      <div class="practice">RV Orthopaedic Specialists</div>
      <div>38517 North Willowmere Ave</div>
      <div>Coral Springs, FL 33071</div>
    </address>
    <span class="contact__divider"></span>
    <div class="contact contact--lines">
      <div class="contact__row">
        <svg viewBox="0 0 16 14" aria-label="Phone"><path d="M1 5c0-2 3-4 7-4s7 2 7 4l-3 1-1-2H5L4 6 1 5zM4 7h8l2 6H2l2-6zm4 1.5a2 2 0 1 0 0 4 2 2 0 0 0 0-4z"/></svg>
        <span>954-218-4063</span>
      </div>
      <div class="contact__row">
        <svg viewBox="0 0 16 14" aria-label="Fax"><path d="M4 0h8v4H4zM1 5h14v6h-3v3H4v-3H1zm4 4v4h6V9zm6-2.5a.8.8 0 1 0 0 1.6.8.8 0 0 0 0-1.6z"/></svg>
        <span>954-582-7341</span>
      </div>
      <div class="contact__row">
        <svg viewBox="0 0 16 14" aria-label="Email"><path d="M1 2h14v1L8 8 1 3zm0 3 7 5 7-5v7H1z"/></svg>
        <span>info@myrvbonecare.example</span>
      </div>
    </div>
  </section>
</body>
</html>
```